Business Cards for IT Consulting Company (Managed Service Provider)

I am looking to have some business cards printed and would like some designs. We are an IT Consulting company based in Vancouver BC. I would like a nice clean and modern look to the cards. I have uploaded all the versions of my logo so parts can be used as needed. Here is a snippit from our website homepage:

Quillbrook Networks Ltd. is an IT Solutions Partner located in Vancouver BC, Canada. We offer IT solutions and support to customers in the greater Vancouver Area. With expertise in Microsoft platforms, as well as Linux and Mac OSX and over 12 years experience in the IT industry, Quillbrook Networks is dedicated to offering our clients top quality service and products. We take pride in the solutions we offer our customers. The greatest compliment a client can give us is to recommend our services.

Quillbrook Networks Ltd. offers a wide range of IT services from onsite service to remote support and managed service solutions. This allows clients to choose the support path that best suits their company’s needs. Supporting many different sized companies from small to enterprise level over the past 12 years Quillbrook Networks has the experience and expertise needed to ensure things run smoothly. Allowing our clients to focus on doing business.

Revolutionizing the way IT services are delivered.

Quillbrook Networks is dedicated to providing our clients with IT solutions that work and grow with them for years to come. This philosophy helps save money in the long run instead of replacing equipment constantly. Far too often IT solutions are not well thought out and while possibly solving the problem at hand, require replacement due to growth or quality within a very short time frame. Quillbrook Networks takes pride in providing solutions that will last and be able to accommodate growth without the need for replacement.

Industry/Entity Type

Information Technology

Contact Information for Business Card

Quillbrook Networks Ltd.
(Employee Name)
Eml: (Employees Email Address)
Web: quillbrook.me
Ph: 604-555-0148

Font styles to use
Serif
Sans Serif

Requirements
Must have
• The Company logo and company colors.
Nice to have
• - Our tag line: "Revolutionizing IT Services" or "Revolutionizing the way IT services are delivered."
• - Also I really like the idea of nature and technology together blending which is sort of where my logo came from so integrating that somehow onto the business cards would be great.

```html
<!DOCTYPE html>
<html lang="en">
<head>
<meta charset="utf-8">
<title>Quillbrook Networks Ltd. — Business Cards</title>
<link href="https://fonts.googleapis.com/css2?family=Montserrat:wght@400;500;600&display=swap" rel="stylesheet">
<style>
  :root {
    --bg: #2b2c2e;
    --paper: #f4f4f4;
    --paper-shade: #e6e6e6;
    --brand-blue: #1ba6dd;
    --ink-grey: #6a6c6f;
    --panel-top: #6d6f72;
    --panel-bottom: #4a4c4f;
    --contact-text: #e9eaeb;
    --photo-warm: #c9924a;
    --photo-cool: #4f7c84;
    --photo-deep: #3a4a52;
  }
  * { box-sizing: border-box; margin: 0; padding: 0; }
  html, body {
    width: 1200px; height: 900px; overflow: hidden;
    background: var(--bg);
    font-family: "Montserrat", sans-serif;
  }
  .canvas {
    width: 1200px; height: 900px;
    display: flex; flex-direction: column;
    align-items: center; justify-content: center; gap: 40px;
  }
  .card {
    position: relative;
    width: 620px; height: 354px;
    background: linear-gradient(180deg, var(--paper), var(--paper-shade));
    overflow: hidden;
  }
  .wordmark {
    display: flex; align-items: center; gap: 14px;
  }
  .wordmark-square {
    width: 34px; height: 34px; border: 3px solid var(--brand-blue);
  }
  .wordmark-name {
    color: var(--brand-blue); font-weight: 500; line-height: 1.05;
  }
  .wordmark-name .line-main { display: block; font-size: 34px; letter-spacing: 0.5px; }
  .wordmark-name .line-sub { display: block; font-size: 13px; letter-spacing: 2px; text-transform: uppercase; }

  /* Front */
  .card-front .wordmark { position: absolute; left: 40px; top: 40px; }
  .card-front .city-photo {
    position: absolute; left: 0; right: 0; top: 132px; height: 190px;
    background:
      radial-gradient(ellipse at 70% 40%, rgba(230,170,80,0.7), transparent 55%),
      radial-gradient(ellipse at 25% 70%, rgba(220,150,60,0.5), transparent 50%),
      linear-gradient(135deg, var(--photo-cool), var(--photo-deep) 45%, var(--photo-warm));
  }
  .card-front .brand-band {
    position: absolute; left: 0; right: 0; bottom: 0; height: 32px;
    background: var(--brand-blue);
  }

  /* Back */
  .card-back .wordmark { position: absolute; right: 38px; top: 36px; }
  .card-back .holder {
    position: absolute; left: 40px; top: 122px;
  }
  .holder-name {
    color: var(--brand-blue); font-weight: 600; font-size: 20px; letter-spacing: 1px; text-transform: uppercase;
  }
  .holder-role {
    color: var(--ink-grey); font-size: 15px; margin-top: 4px;
  }
  .contact-panel {
    position: absolute; left: 0; right: 0; top: 196px; bottom: 30px;
    background: linear-gradient(180deg, var(--panel-top), var(--panel-bottom));
  }
  .contact-panel svg.notch { position: absolute; left: 68px; top: -10px; }
  .contact-list {
    list-style: none; position: absolute; left: 40px; top: 26px;
    display: flex; flex-direction: column; gap: 9px;
  }
  .contact-item {
    display: flex; align-items: center; gap: 12px;
    color: var(--contact-text); font-size: 14px; letter-spacing: 0.3px;
  }
  .contact-icon {
    width: 20px; height: 20px; background: var(--brand-blue); border-radius: 3px;
    display: flex; align-items: center; justify-content: center;
  }
  .card-back .brand-band {
    position: absolute; left: 0; right: 0; bottom: 0; height: 30px;
    background: var(--brand-blue);
  }
</style>
</head>
<body>
<main class="canvas">

  <section class="card card-front">
    <div class="wordmark">
      <span class="wordmark-square"></span>
      <span class="wordmark-name"><span class="line-main">quillbrook</span><span class="line-sub">Networks Ltd.</span></span>
    </div>
    <div class="city-photo" role="img" aria-label="Aerial night view of a downtown city with lit streets and rooftops"></div>
    <div class="brand-band"></div>
  </section>

  <section class="card card-back">
    <div class="wordmark">
      <span class="wordmark-square"></span>
      <span class="wordmark-name"><span class="line-main">quillbrook</span><span class="line-sub">Networks Ltd.</span></span>
    </div>
    <div class="holder">
      <p class="holder-name">Jordan Ellery</p>
      <p class="holder-role">General Manager</p>
    </div>
    <div class="contact-panel">
      <svg class="notch" width="20" height="10" viewBox="0 0 20 10"><path d="M0 10 L10 0 L20 10 Z" fill="var(--panel-top)"/></svg>
      <ul class="contact-list">
        <li class="contact-item">
          <span class="contact-icon"><svg width="12" height="12" viewBox="0 0 24 24"><path d="M6.6 10.8a15 15 0 0 0 6.6 6.6l2.2-2.2a1 1 0 0 1 1-.25 11.4 11.4 0 0 0 3.6.57 1 1 0 0 1 1 1V20a1 1 0 0 1-1 1A17 17 0 0 1 3 4a1 1 0 0 1 1-1h3.5a1 1 0 0 1 1 1c0 1.25.2 2.45.57 3.57a1 1 0 0 1-.25 1z" fill="#fff"/></svg></span>
          604-555-0148
        </li>
        <li class="contact-item">
          <span class="contact-icon"><svg width="12" height="12" viewBox="0 0 24 24"><rect x="2" y="5" width="20" height="14" rx="1" fill="none" stroke="#fff" stroke-width="2.2"/><path d="M2 6 L12 13 L22 6" fill="none" stroke="#fff" stroke-width="2.2"/></svg></span>
          info@quillbrook.me
        </li>
        <li class="contact-item">
          <span class="contact-icon"><svg width="12" height="12" viewBox="0 0 24 24"><circle cx="12" cy="12" r="9.5" fill="none" stroke="#fff" stroke-width="2"/><path d="M2.5 12h19M12 2.5c3 3 3 16 0 19M12 2.5c-3 3-3 16 0 19" fill="none" stroke="#fff" stroke-width="1.8"/></svg></span>
          www.quillbrook.me
        </li>
      </ul>
    </div>
    <div class="brand-band"></div>
  </section>

</main>
</body>
</html>
```